Create a memorable Stationary for Security Software Company

Velbrantix is the worldwide leader in securing the Internet. Making Internet communications and critical data secure, reliable and available everywhere has been and continues to be our ongoing vision. We are committed to staying focused on real customer needs and to developing new and innovative security solutions that redefine the security landscape.

Industry/Entity Type

Internet

Font styles to use
Serif
Sans Serif
Script

Colors
0792cd
33a6d7
85cae6

```html
<!DOCTYPE html>
<html lang="en">
<head>
<meta charset="utf-8">
<title>Velbrantix Stationery</title>
<link href="https://fonts.googleapis.com/css2?family=Open+Sans:wght@400;600;700&family=Merriweather:wght@400&display=swap" rel="stylesheet">
<style>
  :root{
    --blue-dark:#0792cd;
    --blue-mid:#33a6d7;
    --blue-light:#85cae6;
    --paper:#ffffff;
    --ink:#2b2b2b;
    --ink-soft:#6b6b6b;
    --backdrop:#e9eaec;
  }
  *{margin:0;padding:0;box-sizing:border-box}
  html,body{width:1200px;height:3291px;overflow:hidden}
  body{background:var(--backdrop);position:relative;font-family:"Open Sans",Arial,sans-serif;color:var(--ink)}
  .sheet{position:absolute;background:var(--paper);overflow:hidden;box-shadow:0 6px 18px rgba(0,0,0,.12)}
  .sheet .shapes{position:absolute;inset:0;width:100%;height:100%}
  .fill-dark{fill:var(--blue-dark)}
  .fill-mid{fill:var(--blue-mid)}
  .fill-light{fill:var(--blue-light)}
  .brand{position:absolute;display:flex;align-items:center;gap:.35em;font-weight:700;color:var(--blue-dark);line-height:1}
  .brand-dot{width:.8em;height:.8em;border-radius:50%;background:var(--blue-dark)}

  /* letterhead */
  .letterhead{left:50px;top:188px;width:700px;height:990px}
  .letterhead .brand{left:46px;top:30px;font-size:22px}
  .letter-body{position:absolute;left:70px;right:70px;top:170px;font-family:"Merriweather",Georgia,serif;font-size:11.5px;line-height:1.9;color:var(--ink)}
  .letter-body p{margin-bottom:16px;text-align:justify}
  .letter-sign{margin-top:26px}
  .letter-footer{position:absolute;left:300px;bottom:70px;font-size:10px;color:var(--ink-soft);line-height:1.6}
  .letter-footer .tagline{color:var(--blue-dark)}

  /* business cards */
  .card{width:400px;height:229px;left:750px}
  .card-front{top:480px}
  .card-back{top:760px}
  .card-front .brand{left:0;right:0;top:100px;justify-content:center;font-size:30px}
  .card-name{position:absolute;left:26px;top:34px}
  .card-name h2{font-size:17px;font-weight:700;color:var(--ink)}
  .card-name span{font-size:10px;color:var(--ink-soft)}
  .contact-list{position:absolute;left:26px;top:86px;list-style:none;font-size:10px;line-height:1.75;font-weight:600;color:var(--ink)}
  .contact-list li{display:flex;align-items:center;gap:8px}
  .contact-list li::before{content:"";width:7px;height:7px;border-radius:50%;background:var(--blue-dark)}
  .card-back .brand{right:24px;bottom:36px;font-size:20px}

  /* envelope */
  .envelope{left:50px;top:1366px;width:1100px;height:560px}
  .envelope .brand{left:44px;top:40px;font-size:28px}
  .envelope-return{position:absolute;left:44px;bottom:40px;font-size:12px;color:var(--ink-soft);line-height:1.6}
  .envelope-return .tagline{color:var(--blue-dark)}

  /* cover */
  .cover{left:250px;top:2114px;width:700px;height:990px}
  .cover .brand{left:0;right:0;top:460px;justify-content:center;font-size:54px}
</style>
</head>
<body>

<section class="sheet letterhead" aria-label="Letterhead">
  <svg class="shapes" viewBox="0 0 700 990" preserveAspectRatio="none" aria-hidden="true">
    <polygon class="fill-light" points="0,0 700,0 700,130 0,50"/>
    <polygon class="fill-dark" points="480,105 700,130 700,70"/>
    <polygon class="fill-light" points="0,900 700,950 700,990 0,990"/>
    <polygon class="fill-dark" points="0,860 230,915 0,950"/>
  </svg>
  <div class="brand"><span class="brand-dot"></span>Velbrantix</div>
  <div class="letter-body">
    <p>Dear partner, thank you for choosing our team to protect your network. This letter confirms the start of our security review and outlines the next steps we will take together over the coming weeks.</p>
    <p>Our engineers will audit every gateway, update your encryption keys and test each service for weak points. You will receive a short report after each stage, with clear advice and a plan for any fixes.</p>
    <p>Please share access details with your account manager before Monday so the work can begin on time. We look forward to keeping your data safe, reliable and available everywhere.</p>
    <p class="letter-sign">Kind regards,</p>
  </div>
  <div class="letter-footer">
    <div class="tagline">Securing every connection, everywhere.</div>
    <div>12 Harbor Lane, Dunmore, Ohio 4521</div>
    <div>info@velbrantix.com · 1300 555 018</div>
  </div>
</section>

<section class="sheet card card-front" aria-label="Business card front">
  <svg class="shapes" viewBox="0 0 400 229" preserveAspectRatio="none" aria-hidden="true">
    <polygon class="fill-light" points="0,0 400,0 400,12 0,70"/>
    <polygon class="fill-dark" points="250,0 400,0 400,34"/>
    <polygon class="fill-light" points="0,172 400,196 400,229 0,229"/>
    <polygon class="fill-dark" points="0,150 130,182 0,206"/>
  </svg>
  <div class="brand"><span class="brand-dot"></span>Velbrantix</div>
</section>

<section class="sheet card card-back" aria-label="Business card back">
  <svg class="shapes" viewBox="0 0 400 229" preserveAspectRatio="none" aria-hidden="true">
    <polygon class="fill-light" points="400,70 400,229 70,229"/>
    <polygon class="fill-dark" points="200,0 400,0 400,36"/>
    <polygon class="fill-mid" points="0,200 90,229 0,229"/>
  </svg>
  <div class="card-name">
    <h2>Mara Quill</h2>
    <span>Manager</span>
  </div>
  <ul class="contact-list">
    <li>12 Harbor Lane, Dunmore, Ohio 4521</li>
    <li>info@velbrantix.com</li>
    <li>1300 555 018 | (07) 5550 2194</li>
    <li>0400 555 372</li>
    <li>www.velbrantix.com</li>
  </ul>
  <div class="brand"><span class="brand-dot"></span>Velbrantix</div>
</section>

<section class="sheet envelope" aria-label="Envelope">
  <svg class="shapes" viewBox="0 0 1100 560" preserveAspectRatio="none" aria-hidden="true">
    <polygon class="fill-light" points="0,0 560,0 0,210"/>
    <polygon class="fill-light" points="0,240 1100,400 1100,470 0,300"/>
    <polygon class="fill-dark" points="760,420 1100,400 1100,560"/>
  </svg>
  <div class="brand"><span class="brand-dot"></span>Velbrantix</div>
  <div class="envelope-return">
    <div class="tagline">Securing every connection, everywhere.</div>
    <div>12 Harbor Lane, Dunmore, Ohio 4521</div>
  </div>
</section>

<section class="sheet cover" aria-label="Folder cover">
  <svg class="shapes" viewBox="0 0 700 990" preserveAspectRatio="none" aria-hidden="true">
    <polygon class="fill-light" points="0,0 700,0 700,60 0,170"/>
    <polygon class="fill-dark" points="470,0 700,0 700,60"/>
    <polygon class="fill-light" points="0,860 700,760 700,990 0,990"/>
    <polygon class="fill-dark" points="0,840 260,900 0,960"/>
  </svg>
  <div class="brand"><span class="brand-dot"></span>Velbrantix</div>
</section>

</body>
</html>
```